Kor'v Meridell Travel

We need a sleek, professional, inviting card to elicit global travel for the experienced and professional traveler. Royal blue, black and silver. (perhaps the wording could be silver with black shadow?-get creative) Maybe a watermark on the front and the full raised logo on the back.
We want a stylish and modern card, but professional.

```html
<!DOCTYPE html>
<html lang="en">
<head>
<meta charset="utf-8">
<title>Kor'v Meridell Travel – Business Card</title>
<link rel="stylesheet" href="https://fonts.googleapis.com/css2?family=Josefin+Sans:wght@700&family=Arimo:wght@400&display=swap">
<style>
  :root {
    --backdrop: #b8b8b8;
    --royal-blue: #1f44a8;
    --night: #141518;
    --silver: #d4d7dc;
    --silver-deep: #9aa0a8;
    --paper: #f7f8f9;
    --shadow: rgba(0, 0, 0, 0.55);
  }
  * { box-sizing: border-box; margin: 0; padding: 0; }
  html, body {
    width: 1200px;
    height: 801px;
    overflow: hidden;
    background: var(--backdrop);
  }
  .stage { position: relative; width: 1200px; height: 801px; }

  .card {
    position: absolute;
    top: 273px;
    width: 443px;
    height: 264px;
    overflow: hidden;
    box-shadow: 2px 2px 2px var(--shadow);
  }
  .card--front { left: 153px; background: var(--royal-blue); }
  .card--back  { left: 625px; background: var(--paper); }

  .front-bands { position: absolute; inset: 0; }

  .flight-art {
    position: absolute;
    left: 318px;
    top: 54px;
    width: 124px;
    height: 100px;
    background: radial-gradient(ellipse at center, rgba(212, 215, 220, 0.55) 0%, rgba(212, 215, 220, 0) 70%);
  }

  .holder {
    position: absolute;
    left: 24px;
    top: 29px;
    color: var(--silver);
  }
  .holder__name {
    font-family: "Josefin Sans", sans-serif;
    font-weight: 700;
    font-size: 17px;
    line-height: 1;
    text-shadow: 1px 1px 0 var(--night);
  }
  .holder__role {
    font-family: "Arimo", sans-serif;
    font-weight: 400;
    font-size: 12.5px;
    line-height: 1.3;
    margin-top: 1px;
  }

  .front-brand {
    position: absolute;
    left: 24px;
    top: 150px;
    font-family: "Josefin Sans", sans-serif;
    font-weight: 700;
    font-size: 14px;
    letter-spacing: 0.5px;
    color: var(--silver);
  }

  .address {
    position: absolute;
    left: 95px;
    top: 197px;
    font-family: "Arimo", sans-serif;
    font-size: 12.5px;
    line-height: 15.6px;
    color: var(--silver);
    font-style: normal;
  }

  .contacts {
    position: absolute;
    right: 29px;
    top: 182px;
    list-style: none;
    font-family: "Arimo", sans-serif;
    font-size: 12.5px;
    color: var(--silver);
    letter-spacing: 0.3px;
  }
  .contacts__item {
    display: flex;
    align-items: center;
    justify-content: flex-end;
    gap: 4px;
    height: 15.6px;
  }
  .contacts__icon { width: 12px; height: 12px; flex: none; }

  .brand-name {
    position: absolute;
    left: 0;
    right: 0;
    top: 118px;
    text-align: center;
    font-family: "Josefin Sans", sans-serif;
    font-weight: 700;
    font-size: 24px;
    letter-spacing: 0.5px;
    color: var(--royal-blue);
  }
  .brand-rule {
    position: absolute;
    left: 97px;
    right: 97px;
    top: 160px;
    height: 1px;
    background: var(--silver-deep);
  }
</style>
</head>
<body>
<main class="stage">

  <section class="card card--front" aria-label="Card front">
    <svg class="front-bands" width="443" height="264" viewBox="0 0 443 264" aria-hidden="true">
      <defs>
        <linearGradient id="band-night" x1="0" y1="0" x2="0" y2="1">
          <stop offset="0" stop-color="#26282d"/>
          <stop offset="1" stop-color="#0e0f12"/>
        </linearGradient>
      </defs>
      <rect width="443" height="264" fill="var(--royal-blue)"/>
      <polygon points="0,124 443,104 443,264 0,264" fill="url(#band-night)"/>
      <line x1="0" y1="124" x2="443" y2="104" stroke="var(--silver-deep)" stroke-width="1.2"/>
    </svg>

    <div class="flight-art" role="img" aria-label="Airliner in flight, drawn in silver"></div>

    <header class="holder">
      <h1 class="holder__name">ADRIAN VELL</h1>
      <p class="holder__role">Managing Director</p>
    </header>

    <p class="front-brand">KOR'V MERIDELL TRAVEL</p>

    <address class="address">
      421, Address line<br>
      goes here<br>
      45452,Country Name
    </address>

    <ul class="contacts">
      <li class="contacts__item">044-123 456 789
        <svg class="contacts__icon" viewBox="0 0 12 12" aria-hidden="true">
          <rect width="12" height="12" rx="2" fill="var(--silver)"/>
          <path d="M3.5 2.5l1.5 0.3 0.6 1.8-1 0.8a5 5 0 0 0 2.5 2.5l0.8-1 1.8 0.6 0.3 1.5-1 0.9C5.5 9.6 2.4 6.5 2.6 3.5z" fill="var(--night)"/>
        </svg>
      </li>
      <li class="contacts__item">044-123 456 789
        <svg class="contacts__icon" viewBox="0 0 12 12" aria-hidden="true">
          <rect width="12" height="12" rx="2" fill="var(--silver)"/>
          <rect x="3.5" y="2" width="5" height="8" rx="0.8" fill="none" stroke="var(--night)" stroke-width="1.2"/>
          <circle cx="6" cy="8.6" r="0.5" fill="var(--night)"/>
        </svg>
      </li>
      <li class="contacts__item">info@korvmeridell.com
        <svg class="contacts__icon" viewBox="0 0 12 12" aria-hidden="true">
          <rect width="12" height="12" rx="2" fill="var(--silver)"/>
          <rect x="2" y="3.2" width="8" height="5.6" fill="none" stroke="var(--night)" stroke-width="1"/>
          <path d="M2 3.2l4 3 4-3" fill="none" stroke="var(--night)" stroke-width="1"/>
        </svg>
      </li>
      <li class="contacts__item">www.korvmeridell.com
        <svg class="contacts__icon" viewBox="0 0 12 12" aria-hidden="true">
          <rect width="12" height="12" rx="2" fill="var(--silver)"/>
          <g fill="none" stroke="var(--night)" stroke-width="0.9">
            <circle cx="6" cy="6" r="3.8"/>
            <ellipse cx="6" cy="6" rx="1.6" ry="3.8"/>
            <path d="M2.2 6h7.6M2.8 4h6.4M2.8 8h6.4"/>
          </g>
        </svg>
      </li>
    </ul>
  </section>

  <section class="card card--back" aria-label="Card back">
    <p class="brand-name">KOR'V MERIDELL TRAVEL</p>
    <div class="brand-rule" aria-hidden="true"></div>
  </section>

</main>
</body>
</html>
```